Resposive web site in 4 languages + image gallery + logo design

We need a web page, which will work on all devices.
I have uploaded web page concept.
Company name: Praxelun
Industry/Entity Type
It Company
Logo Text
quality matters
Coding
Coded - Design and coding required
Number of Pages Required
1 page

```html
<!DOCTYPE html>
<html lang="en">
<head>
<meta charset="utf-8">
<title>Praxelun</title>
<link href="https://fonts.googleapis.com/css2?family=Raleway:wght@400;500;600&family=Open+Sans:wght@400;600&display=swap" rel="stylesheet">
<style>
:root{
  --orange:#ffa200;
  --orange-deep:#f08a1c;
  --ink:#3a3a3a;
  --muted:#8a8a8a;
  --white:#ffffff;
  --stone:#4f4d4b;
  --dark:#2f2f2f;
  --footer:#2a2a2a;
  --tab-line:#c9c9c9;
}
*{box-sizing:border-box;margin:0;padding:0}
html,body{width:1200px;height:2546px;overflow:hidden;background:var(--white)}
body{position:relative;font-family:'Open Sans',sans-serif;color:var(--ink)}
.abs{position:absolute}
.heading{font-family:'Raleway',sans-serif;font-weight:500}

/* hero */
.hero{left:0;top:0;width:1200px;height:567px;background:linear-gradient(120deg,#5a4a3c 0%,#7a6552 40%,#4e4036 75%,#3a3029 100%)}
.brand{left:187px;top:30px;font-family:'Raleway',sans-serif;font-size:34px;font-weight:400;color:var(--white)}
.nav{top:42px;font-family:'Raleway',sans-serif;font-size:15px;color:var(--white)}
.lang{left:893px;top:36px;width:90px;height:28px;border:1px solid #cfcfcf;background:rgba(0,0,0,.35);color:var(--white);font-size:11px;display:flex;align-items:center;gap:6px;padding-left:8px}
.lang i{display:block;width:14px;height:10px;background:#d8d8d8}
.social-dot{left:996px;top:34px;width:32px;height:32px;border-radius:50%;border:2px solid var(--white)}
.hero-title{left:0;width:1200px;text-align:center;color:var(--white);font-family:'Raleway',sans-serif;font-weight:400}
.cta{left:531px;top:344px;width:139px;height:40px;background:var(--orange);color:var(--white);font-family:'Raleway',sans-serif;font-weight:600;font-size:14px;display:flex;align-items:center;justify-content:center}
.dots{left:565px;top:506px;display:flex;gap:4px}
.dots span{width:16px;height:16px;border-radius:50%;background:var(--white)}
.dots span.on{background:var(--orange);border:2px solid var(--white)}

/* services */
.section-title{left:0;width:1200px;text-align:center;font-family:'Raleway',sans-serif;font-size:29px;color:var(--orange);font-weight:500}
.photo{border:0}
.photo .frame{position:absolute;left:10px;top:14px;right:-12px;bottom:-6px;border:2px solid var(--white)}
.svc-title{font-family:'Raleway',sans-serif;font-size:22px;font-weight:500;color:var(--ink)}
.svc-text{font-size:12px;line-height:22px;color:var(--muted);width:450px}
.svc-text p+p{margin-top:10px}
.tabs{display:grid;height:38px;border:1px solid var(--tab-line);background:linear-gradient(#ffffff,#ededed)}
.tabs span{display:flex;align-items:center;justify-content:center;font-family:'Raleway',sans-serif;font-size:16px;color:var(--ink);border-right:1px solid var(--tab-line)}
.tabs span:last-child{border-right:0}
.band-stone{left:0;top:983px;width:1200px;height:361px;background:linear-gradient(135deg,#5c5a57,#48474a 50%,#555250)}
.band-stone .svc-title,.band-stone .svc-text{color:var(--white)}
.tabs.dark{background:#262626;border-color:#555}
.tabs.dark span{color:var(--white);border-color:#555}

/* about */
.about{left:0;top:1741px;width:1200px;height:377px;background:var(--orange)}
.about-title{left:0;top:1792px;width:1200px;text-align:center;font-family:'Raleway',sans-serif;font-size:32px;color:var(--white)}
.ring{left:197px;top:1832px;width:228px;height:228px;border-radius:50%;border:2px solid var(--white)}
.ring .inner{position:absolute;left:12px;top:12px;width:200px;height:200px;border-radius:50%;background:linear-gradient(140deg,#6b4a2e,#b7874e 55%,#d7b58a)}
.about-text{left:473px;top:1858px;width:520px;color:var(--white);font-size:12.5px;line-height:22px}
.about-text p+p{margin-top:18px}

/* contact */
.contact{left:0;top:2118px;width:1200px;height:373px;background:linear-gradient(120deg,#3c3c3c,#2e2e2e 50%,#3a3836)}
.contact-title{left:212px;top:2174px;font-family:'Raleway',sans-serif;font-size:29px;color:var(--white)}
.address{left:212px;top:2228px;color:var(--white);font-size:15px;line-height:27px;font-style:normal}
.icons{left:212px;top:2383px;display:flex;gap:6px}
.icons span{width:26px;height:26px;border-radius:50%;border:2px solid var(--white)}
.form-title{left:618px;top:2175px;width:380px;color:var(--white);font-family:'Raleway',sans-serif;font-size:17px;line-height:22px}
.field{left:616px;width:373px;background:var(--white);font-size:9px;color:#777;padding:7px 12px;letter-spacing:.5px}
.send{left:614px;top:2420px;width:85px;height:31px;background:var(--orange-deep);color:var(--white);font-family:'Raleway',sans-serif;font-size:13px;font-weight:600;display:flex;align-items:center;justify-content:center}
.footer{left:0;top:2491px;width:1200px;height:55px;background:var(--footer)}
.footer p{position:absolute;left:192px;top:20px;color:#9a9a9a;font-size:10px}
</style>
</head>
<body>

<header>
  <div class="abs hero" role="img" aria-label="Craftsman in safety glasses cutting timber in a woodworking shop"></div>
  <div class="abs brand">Praxelun</div>
  <nav>
    <span class="abs nav" style="left:557px">SERVICES</span>
    <span class="abs nav" style="left:667px">ABOUT US</span>
    <span class="abs nav" style="left:782px">CONTACT</span>
  </nav>
  <div class="abs lang"><i></i>English &#8964;</div>
  <div class="abs social-dot"></div>
  <h1 class="abs hero-title" style="top:222px;font-size:45px">ARE YOU INTERESTED IN</h1>
  <h2 class="abs hero-title" style="top:280px;font-size:37px">AN ESTIMATE?</h2>
  <div class="abs cta">GET A QUOTE</div>
  <div class="abs dots"><span class="on"></span><span></span><span></span><span></span></div>
</header>

<main>
  <h2 class="abs section-title" style="top:608px">OUR SERIVCES</h2>

  <section class="service">
    <div class="abs photo" style="left:192px;top:689px;width:310px;height:187px;background:linear-gradient(135deg,#6e4a2d,#b8895a 55%,#e2c9a2)" role="img" aria-label="Hands working a hand plane over timber with wood shavings"><div class="frame"></div></div>
    <h3 class="abs svc-title" style="left:531px;top:695px">WOODWORKS</h3>
    <div class="abs svc-text" style="left:535px;top:734px">
      <p>Timber is, in essence, a natural and warm material. Wood is also relatively durable and easy to work with, which has made it a favourite of builders throughout history.</p>
      <p>Our goal is to offer suitable products and quality furniture with installation and after-sales service to all of our clients. In order to achieve this, we're ready to help our clients in all stages of construction from design to production and maintenance.</p>
    </div>
    <div class="abs tabs" style="left:202px;top:911px;width:782px;grid-template-columns:103px 137px 100px 146px 149px 1fr">
      <span>Furniture</span><span>Windows</span><span>Doors</span><span>Staircases</span><span>Woodcarving</span><span>Graining</span>
    </div>
  </section>

  <section class="abs band-stone" role="img" aria-label="Stone paving path in a garden"></section>
  <section class="service">
    <h3 class="abs svc-title" style="left:199px;top:1058px;color:var(--white)">STONEWORKS</h3>
    <div class="abs svc-text" style="left:199px;top:1096px;color:var(--white);width:430px">
      <p>The natural stone found in the ground has been used in construction for centuries because of its durability. A structure built by a skilled craftsman from natural stone is unique, genuine and durable, and perfect for our bracing climate.</p>
      <p style="margin-top:20px">Our experienced craftsmen are ready to help you in all stages of construction from planning to completion.</p>
    </div>
    <div class="abs photo" style="left:679px;top:1049px;width:309px;height:185px;background:linear-gradient(135deg,#8d8f94,#5f6268 50%,#b3b4b6)" role="img" aria-label="Gloved hands laying paving stones with a rubber mallet"><div class="frame" style="left:6px;top:6px;right:6px;bottom:6px"></div></div>
    <div class="abs tabs dark" style="left:199px;top:1271px;width:782px;grid-template-columns:110px 90px 80px 153px 107px 105px 1fr">
      <span>Walls</span><span>Terraces</span><span>Paths</span><span>Outdoor kitchens</span><span>Fireplaces</span><span>Smokeries</span><span>Fences</span>
    </div>
  </section>

  <section class="service">
    <div class="abs photo" style="left:199px;top:1398px;width:310px;height:187px;background:linear-gradient(135deg,#5a3a22,#9a6a3c 50%,#d4b48e)" role="img" aria-label="Hand restoring the back of a wooden chair with a tool"><div class="frame" style="left:6px;top:6px;right:6px;bottom:6px"></div></div>
    <h3 class="abs svc-title" style="left:546px;top:1402px">RESTORATION</h3>
    <div class="abs svc-text" style="left:548px;top:1441px;width:440px">
      <p>It's good to see that fixing old things has become popular again in recent years and people are trying to find ways to preserve valuable old windows and pieces of furniture before deciding to replace them.</p>
      <p>It is possible to give a new life to almost any wooden door, window, piece of furniture or staircase. The extensive experience of our craftsmen will help you achieve the desired result.</p>
    </div>
    <div class="abs tabs" style="left:207px;top:1624px;width:782px;grid-template-columns:139px 141px 85px 132px 105px 1fr">
      <span>Furniture</span><span>Windows</span><span>Doors</span><span>Staircases</span><span>Floors</span><span>Special Projects</span>
    </div>
  </section>

  <section class="abs about"></section>
  <h2 class="abs about-title">ABOUT US</h2>
  <div class="abs ring"><div class="inner" role="img" aria-label="Hands working a hand plane over timber"></div></div>
  <div class="abs about-text">
    <p>Praxelun is a company whose business operations include making wooden products, restoration and building structures from natural stone</p>
    <p>All of our products are made by craftsmen and specialists who have extensive experience and knowledge in their fields. The products we offer are always handmade and we take the requests and ideas of the specific client into account. We always strive to achieve the best possible quality.</p>
    <p style="margin-top:14px">Quality matters,<br>Praxelun</p>
  </div>

  <section class="abs contact" role="img" aria-label="Hands at a keyboard beside papers on a desk"></section>
  <h2 class="abs contact-title">CONTACT US</h2>
  <address class="abs address">Vellamo 12<br>00412 Korvala<br>NORDLAND<br>Telephone: +000 55 01234<br>e-mail: info@praxelun.example</address>
  <div class="abs icons"><span></span><span></span><span></span><span></span></div>

  <p class="abs form-title">Please Fill in the Following Fields If you would like a Price Quote</p>
  <div class="abs field" style="top:2231px;height:28px">NAME</div>
  <div class="abs field" style="top:2264px;height:29px">PHONE</div>
  <div class="abs field" style="top:2298px;height:29px">EMAIL</div>
  <div class="abs field" style="top:2333px;height:77px">MESSAGE</div>
  <div class="abs send">SEND</div>
</main>

<footer class="abs footer"><p>© 2016 Company Name &nbsp;All right reserved &nbsp;Term of Use</p></footer>

</body>
</html>
```